Vantor Wear and Fuel is looking for a Clothing/Supplement Online Store Website!

Must be convenient, and user friendly, with vibrant colors that catch the eye!

Target Market(s)

Athletes, and Fashion Customers

Industry/Entity Type

Fitness

Coding

Coded - Design and coding required

Number of Pages Required

3 page

Font styles to use
Decorative

Colors

Designer to choose colors to be used in the design.

Requirements
Must have
• Somewhere to feature products, features to promote discounts and make announcements.
Nice to have
• My logos on each page

```html
<!DOCTYPE html>
<html lang="en">
<head>
<meta charset="utf-8">
<title>Vantor Wear and Fuel</title>
<link rel="stylesheet" href="https://fonts.googleapis.com/css2?family=Exo+2:wght@500;600;700;800&family=Lato:wght@400;700&display=swap">
<style>
:root{
  --ink:#1c1c1c;
  --text:#3a3a3a;
  --muted:#8a8a8a;
  --line:#d6d6d6;
  --paper:#ffffff;
  --mist:#ececec;
  --night:#2b2b2b;
  --accent:#f2d21c;
  --pink:#e0226e;
  --teal:#2aa7b5;
}
*{box-sizing:border-box;margin:0;padding:0}
html,body{width:1200px;height:3582px;overflow:hidden}
body{position:relative;background:var(--paper);font-family:"Lato",sans-serif;color:var(--text)}
.abs{position:absolute}
.heading{font-family:"Exo 2",sans-serif}

/* header */
.search{left:171px;top:24px;width:253px;height:36px;border:1px solid var(--line);border-radius:18px;font-size:10px;font-style:italic;color:var(--muted);padding:11px 12px}
.search svg{position:absolute;right:12px;top:11px}
.brand{font-family:"Exo 2",sans-serif;font-weight:600;color:#4a4a4a;letter-spacing:1px}
.header-brand{left:500px;top:48px;width:200px;text-align:center;font-size:42px;line-height:1}
.cart{left:793px;top:31px;font-size:14px;font-weight:700;color:var(--ink);display:flex;align-items:center;gap:6px}
.cart .price{color:#b5b5b5;font-weight:400;margin-right:8px}
.cart .dot{width:26px;height:26px;border-radius:50%;background:#3b3b3b;display:flex;align-items:center;justify-content:center}
.nav a{position:absolute;top:100px;font-family:"Exo 2",sans-serif;font-weight:600;font-size:14px;color:var(--ink);text-decoration:none}
.nav .active::after{content:"";position:absolute;left:0;top:30px;width:36px;height:3px;background:var(--ink)}

/* hero */
.hero-band{left:0;top:143px;width:1200px;height:1155px;background:var(--mist)}
.hero{left:0;top:143px;width:1200px;height:727px;
  background:
    radial-gradient(ellipse 210px 150px at 800px 480px,#c9b493 0%,#9c8463 45%,rgba(90,60,40,0) 100%),
    radial-gradient(ellipse 230px 120px at 790px 560px,#7a4a2c 0%,rgba(80,45,25,0) 100%),
    radial-gradient(ellipse 140px 330px at 1030px 300px,#8e8a86 0%,#5a5652 45%,rgba(40,38,36,0) 100%),
    radial-gradient(ellipse 180px 220px at 330px 140px,#6d5547 0%,rgba(60,45,38,0) 100%),
    radial-gradient(ellipse 260px 110px at 520px 560px,#2a2a2c 0%,rgba(20,20,20,0) 100%),
    linear-gradient(180deg,#1a1716 0%,#221e1c 60%,#4a3e33 100%);
  clip-path:polygon(0 0,100% 0,100% 605px,50% 727px,0 605px)}
.offer{left:171px;top:336px;width:445px;height:268px;border:4px solid #fff;color:#fff;font-family:"Exo 2",sans-serif}
.offer .l1{position:absolute;left:54px;top:44px;font-size:50px;font-weight:700;line-height:1.1}
.offer .pct{position:absolute;left:46px;top:108px;font-size:104px;font-weight:800;line-height:1}
.offer .sale{position:absolute;left:265px;top:110px;font-size:58px;font-weight:700;line-height:1.1}
.offer .today{position:absolute;left:270px;top:184px;font-size:18px;font-weight:600;letter-spacing:2px}
.dots{left:577px;top:795px;display:flex;gap:4px}
.dots span{width:13px;height:13px;border-radius:50%;background:#9a9a9a}
.dots span:last-child{background:#fff}

/* about */
.about-img{left:215px;top:950px;width:355px;height:258px;background:linear-gradient(135deg,#3a2a3a,#9c2b4b 45%,#b23858 60%,#2a2030);clip-path:polygon(0 100%,45% 0,100% 0,55% 100%)}
.section-title{font-family:"Exo 2",sans-serif;font-weight:700;color:var(--ink)}
.about-title{left:595px;top:965px;font-size:30px;line-height:1}
.about-copy{left:596px;top:1020px;width:420px;font-size:11px;line-height:21px}
.btn-dark{left:596px;top:1164px;width:117px;height:43px;background:var(--ink);color:#fff;font-size:12px;font-weight:700;display:flex;align-items:center;justify-content:center}

/* products */
.center-title{left:0;width:1200px;text-align:center;font-size:32px;line-height:1}
.center-copy{left:330px;width:540px;text-align:center;font-size:11px;line-height:21px}
.card{width:199px;height:313px;border:1px solid var(--line);background:#fff}
.card::after{content:"";position:absolute;right:-1px;bottom:-1px;width:120px;height:12px;background:#d9d9d9;clip-path:polygon(100% 0,100% 100%,0 100%)}
.card.hot::after{background:var(--ink)}
.card .pic{position:absolute;left:22px;top:18px;width:155px;height:136px;border-radius:6px}
.card .price{position:absolute;top:170px;width:100%;text-align:center;font-family:"Exo 2",sans-serif;font-weight:600;font-size:16px;color:var(--ink)}
.card .desc{position:absolute;top:200px;left:20px;right:20px;text-align:center;font-size:11.5px;line-height:19px;color:#555}
.card .buy{position:absolute;top:253px;left:59px;width:82px;height:27px;border:1px solid #bbb;font-size:10px;display:flex;align-items:center;justify-content:center;color:#555}
.card.hot .buy{background:var(--ink);border-color:var(--ink);color:#fff;font-weight:700}
.badge{position:absolute;left:10px;top:24px;width:40px;height:40px;border-radius:50%;background:var(--pink);color:#fff;font-size:10px;font-weight:700;display:flex;align-items:center;justify-content:center}

/* discounts */
.deal{left:171px;top:2449px;width:418px;height:426px;
  background:
    radial-gradient(ellipse 90px 190px at 95px 200px,#2a2a2e 0%,#1a1a1c 60%,rgba(26,26,28,0) 100%),
    linear-gradient(135deg,#4a3d33,#241f1b 55%,#3a3029)}
.deal .t1{position:absolute;left:215px;top:205px;font-size:34px;font-weight:700;color:#fff;line-height:1.1}
.deal .t2{position:absolute;left:175px;top:245px;font-size:56px;font-weight:800;color:#fff;line-height:1.1}
.deal .t3{position:absolute;left:205px;top:330px;font-size:25px;font-weight:700;color:var(--accent);line-height:1.1}
.promo1{left:607px;top:2449px;width:419px;height:203px;
  background:
    radial-gradient(ellipse 90px 100px at 320px 100px,#f4cdb4 0%,#e8a98e 40%,rgba(70,183,194,0) 100%),
    linear-gradient(90deg,#2a9fae,#46b7c2)}
.promo1 .a{position:absolute;left:38px;top:62px;font-size:22px;font-weight:700;color:#fff;line-height:22px}
.promo1 .code{position:absolute;left:38px;top:124px;width:114px;height:34px;border:2px dashed var(--accent);color:var(--accent);font-size:17px;font-weight:700;display:flex;align-items:center;justify-content:center}
.promo2{left:607px;top:2672px;width:419px;height:203px;
  background:
    radial-gradient(ellipse 80px 60px at 320px 45px,#c21e5e 0%,rgba(194,30,94,0) 100%),
    radial-gradient(ellipse 110px 60px at 320px 150px,#ff5a5a 0%,rgba(255,90,90,0) 100%),
    linear-gradient(90deg,#707070,#5d5d5d 55%,#8a6a70 100%)}
.promo2 .a{position:absolute;left:30px;top:78px;font-size:20px;font-weight:700;color:#fff;line-height:22px}
.promo2 .a em{font-style:normal;color:var(--accent)}

/* service band & footer */
.band{left:0;top:3012px;width:1200px;height:185px;background:var(--night);clip-path:polygon(0 0,100% 0,100% 115px,50% 185px,0 115px)}
.service{top:3068px;display:flex;align-items:center;gap:10px;color:#fff}
.service b{display:block;font-family:"Exo 2",sans-serif;font-size:16px}
.service span{font-size:11px;color:#ddd}
.foot-brand{left:178px;top:3290px;font-size:40px}
.contact{left:171px;top:3396px;display:flex;align-items:center;gap:6px;font-family:"Exo 2",sans-serif;color:var(--ink)}
.contact .ring{width:36px;height:36px;border:2px solid #444;border-radius:50%;display:flex;align-items:center;justify-content:center}
.contact small{display:block;font-size:16px;font-weight:600}
.contact strong{font-size:20px;font-weight:700}
.col{top:3258px;width:140px}
.col h4{font-family:"Exo 2",sans-serif;font-weight:500;font-size:15px;color:#444}
.col h4::after{content:"";display:block;width:20px;height:2px;background:#444;margin-top:14px;margin-bottom:12px}
.col p{font-size:10.5px;line-height:19px;color:#444}
.rule{left:174px;top:3503px;width:876px;height:1px;background:#ccc}
.social{left:171px;top:3536px;display:flex;gap:28px}
.social span{width:20px;height:20px;border-radius:50%;background:#2f2f2f}
.copy{left:643px;top:3541px;font-size:11px;color:#333}
</style>
</head>
<body>

<header>
  <div class="abs search">Enter Keyword..
    <svg width="12" height="12" viewBox="0 0 12 12"><circle cx="5" cy="5" r="3.8" fill="none" stroke="#333" stroke-width="1.6"/><path d="M8 8l3 3" stroke="#333" stroke-width="1.8"/></svg>
  </div>
  <div class="abs brand header-brand">VANTOR</div>
  <div class="abs cart">Shopping Cart <span class="price">$0.00</span>
    <span class="dot"><svg width="12" height="12" viewBox="0 0 12 12"><path d="M1 2h2l1.5 6h5.5l1-4H4" fill="none" stroke="#fff" stroke-width="1.3"/><circle cx="5" cy="10" r="1" fill="#fff"/><circle cx="9" cy="10" r="1" fill="#fff"/></svg></span>
    <span class="dot"><svg width="12" height="12" viewBox="0 0 12 12"><circle cx="6" cy="4" r="2.5" fill="#fff"/><path d="M1.5 11.5c0-3 2-4.5 4.5-4.5s4.5 1.5 4.5 4.5z" fill="#fff"/></svg></span>
    <span class="dot"><svg width="12" height="12" viewBox="0 0 12 12"><path d="M6 11L1.5 6.2A2.6 2.6 0 016 2.8a2.6 2.6 0 014.5 3.4z" fill="#fff"/></svg></span>
  </div>
  <nav class="nav">
    <a class="active" href="#" style="left:172px">HOME</a>
    <a href="#" style="left:254px">ABOUT</a>
    <a href="#" style="left:335px">PRODUCTS</a>
    <a href="#" style="left:781px">REVIEWS</a>
    <a href="#" style="left:877px">BLOG</a>
    <a href="#" style="left:948px">CONTACT US</a>
  </nav>
</header>

<div class="abs hero-band"></div>
<section class="abs hero" role="img" aria-label="Athlete seated behind a shaker bottle, weight plates and a wooden bowl of protein powder with a scoop"></section>
<div class="abs offer">
  <div class="l1">NEW PRODUCT</div>
  <div class="pct">25%</div>
  <div class="sale">SALE</div>
  <div class="today">OFFER TODAY</div>
</div>
<div class="abs dots"><span></span><span></span><span></span></div>

<section>
  <div class="abs about-img" role="img" aria-label="Woman in a red hoodie framed inside an angular shape"></div>
  <h2 class="abs section-title about-title">ABOUT VANTOR</h2>
  <p class="abs about-copy">Lorem ipsum dolor sit amet, consectetur adipiscing elit, sed do eiusmod tempor incididunt ut labore et dolore magna aliqua. Ut enim ad minim veniam, quis nostr ud exercitation ullamco laboris nisi ut aliquip ex ea commodo consequat. Duis ute irure dolor in reprehenderit in voluptate velit esse cillum dolore eu fugiat nulla pariatur. Excepteur sint occaecat cupidatat non proident, sunt in culpa qui fficia deserunt mollit an</p>
  <div class="abs btn-dark">READ MORE</div>
</section>

<section>
  <h2 class="abs section-title center-title" style="top:1380px">FEATURE PRODUCTS</h2>
  <p class="abs center-copy" style="top:1425px">Lorem ipsum dolor sit amet, consectetur adipiscing elit, sed do eiusmod tempor incididunt ut labore et dolore magna aliqua. Ut enim ad minim veniam, quis nostrud exercitation ullamco labor</p>

  <div class="abs card hot" style="left:171px;top:1501px"><div class="pic" role="img" aria-label="Red sports bra" style="background:linear-gradient(160deg,#f0476c,#d3163f 55%,#a80f32)"></div><div class="price">$250.00</div><div class="desc">Lorem ipsum dolor sit ame consec dum loetetudc</div><div class="buy">BUY NOW</div></div>
  <div class="abs card" style="left:389px;top:1501px"><div class="pic" role="img" aria-label="White long sleeve shirt" style="background:linear-gradient(160deg,#fafafa,#e4e4e4 60%,#cfcfcf)"></div><div class="badge">SALE</div><div class="price">$250.00</div><div class="desc">Lorem ipsum dolor sit ame consec dum loetetudc</div><div class="buy">BUY NOW</div></div>
  <div class="abs card" style="left:608px;top:1501px"><div class="pic" role="img" aria-label="Black training shorts" style="background:linear-gradient(160deg,#3a3a3a,#161616 60%,#0a0a0a)"></div><div class="price">$250.00</div><div class="desc">Lorem ipsum dolor sit ame consec dum loetetudc</div><div class="buy">BUY NOW</div></div>
  <div class="abs card" style="left:827px;top:1501px"><div class="pic" role="img" aria-label="Pink crop top" style="background:linear-gradient(160deg,#fb9ccb,#ee5ea4 55%,#d63c88)"></div><div class="price">$250.00</div><div class="desc">Lorem ipsum dolor sit ame consec dum loetetudc</div><div class="buy">BUY NOW</div></div>

  <div class="abs card" style="left:171px;top:1846px"><div class="pic" role="img" aria-label="Black supplement tub" style="background:linear-gradient(160deg,#4a4a4a,#1c1c1c 55%,#0c0c0c)"></div><div class="price">$250.00</div><div class="desc">Lorem ipsum dolor sit ame consec dum loetetudc</div><div class="buy">BUY NOW</div></div>
  <div class="abs card" style="left:389px;top:1846px"><div class="pic" role="img" aria-label="Grey sports bra" style="background:linear-gradient(160deg,#e6e6e6,#bdbdbd 55%,#9a9a9a)"></div><div class="price">$250.00</div><div class="desc">Lorem ipsum dolor sit ame consec dum loetetudc</div><div class="buy">BUY NOW</div></div>
  <div class="abs card" style="left:608px;top:1846px"><div class="pic" role="img" aria-label="Camouflage sports bra" style="background:linear-gradient(160deg,#5a6a70,#34444c 55%,#1f2a30)"></div><div class="price">$250.00</div><div class="desc">Lorem ipsum dolor sit ame consec dum loetetudc</div><div class="buy">BUY NOW</div></div>
  <div class="abs card" style="left:827px;top:1846px"><div class="pic" role="img" aria-label="White supplement bottle" style="background:linear-gradient(160deg,#ffffff,#ececec 55%,#d2d2d2)"></div><div class="price">$250.00</div><div class="desc">Lorem ipsum dolor sit ame consec dum loetetudc</div><div class="buy">BUY NOW</div></div>
</section>

<section>
  <h2 class="abs section-title center-title" style="top:2326px">OUR DISCOUNTS</h2>
  <p class="abs center-copy" style="top:2371px">Lorem ipsum dolor sit amet, consectetur adipiscing elit, sed do eiusmod tempor incididunt ut labore et dolore magna aliqua. Ut enim ad minim veniam, quis nostrud exercitation ullamco labor</p>

  <div class="abs deal heading" role="img" aria-label="Black shaker bottle with a measuring tape and capsules on a dark table">
    <div class="t1">DEAL OF</div>
    <div class="t2">THE DAY</div>
    <div class="t3">GET 80% OFF</div>
  </div>
  <div class="abs promo1 heading" role="img" aria-label="Smiling woman in sunglasses holding shopping bags on a teal backdrop">
    <div class="a">UPTO 30%<br><span style="font-size:18px">ALL PRODUCTS</span></div>
    <div class="code">XGD342G</div>
  </div>
  <div class="abs promo2 heading" role="img" aria-label="Pink sports bra and coral shorts laid out on grey">
    <div class="a">GET <em>50%</em> OFF<br><span style="font-size:17px">NEW COLLECTION</span></div>
  </div>
</section>

<div class="abs band"></div>
<div class="abs service" style="left:168px">
  <svg width="48" height="56" viewBox="0 0 48 56"><rect x="4" y="4" width="40" height="40" rx="6" fill="#fff"/><rect x="10" y="10" width="28" height="14" fill="#2b2b2b"/><rect x="4" y="44" width="9" height="8" fill="#fff"/><rect x="35" y="44" width="9" height="8" fill="#fff"/><circle cx="12" cy="34" r="3" fill="#2b2b2b"/><circle cx="36" cy="34" r="3" fill="#2b2b2b"/></svg>
  <div><b>Free Shipping</b><span>Ducimus qui blanditiis</span></div>
</div>
<div class="abs service" style="left:388px">
  <svg width="40" height="50" viewBox="0 0 40 50"><path d="M10 22V14a10 10 0 0120 0v8" fill="none" stroke="#fff" stroke-width="5"/><rect x="3" y="22" width="34" height="26" rx="3" fill="#fff"/></svg>
  <div><b>100% Secure</b><span>Ducimus qui blanditiis</span></div>
</div>
<div class="abs service" style="left:600px">
  <svg width="60" height="40" viewBox="0 0 60 40"><rect x="8" y="3" width="44" height="28" rx="2" fill="none" stroke="#fff" stroke-width="3"/><path d="M2 35h56v3H2z" fill="#fff"/></svg>
  <div><b>Best Online</b><span>Ducimus qui blanditiis</span></div>
</div>
<div class="abs service" style="left:824px">
  <svg width="60" height="50" viewBox="0 0 60 50"><circle cx="30" cy="12" r="9" fill="#fff"/><circle cx="12" cy="18" r="7" fill="#fff"/><circle cx="48" cy="18" r="7" fill="#fff"/><path d="M14 48c0-12 7-18 16-18s16 6 16 18z" fill="#fff"/><path d="M0 44c0-9 5-14 12-14s10 4 10 6L14 44z" fill="#fff"/><path d="M60 44c0-9-5-14-12-14s-10 4-10 6l8 8z" fill="#fff"/></svg>
  <div><b>Customer Support</b><span>Ducimus qui blanditiis</span></div>
</div>

<footer>
  <div class="abs brand foot-brand">VANTOR</div>
  <div class="abs contact">
    <span class="ring"><svg width="16" height="16" viewBox="0 0 16 16"><path d="M3 1l3 3-2 2a9 9 0 006 6l2-2 3 3-2 2C7 15 1 9 1 3z" fill="#333"/></svg></span>
    <div><small>Contact Us:</small><strong>(125)-555-0148</strong></div>
  </div>
  <div class="abs col" style="left:436px"><h4>Brands</h4><p>Lorem ipsum<br>Dolor sit amet<br>Cnsectetur<br>Adipiscing eli<br>Sed do eiusmod<br>Dtempo<br>Sed do eiusmo</p></div>
  <div class="abs col" style="left:602px"><h4>Company</h4><p>About Us<br>Product Reviews<br>Site Map<br>Discount Policies<br>Advanced Search<br>Affiliate<br>News</p></div>
  <div class="abs col" style="left:767px"><h4>My Account</h4><p>My Account<br>Order History<br>Wish List<br>Newsletter<br>Our Products<br>Nutrition</p></div>
  <div class="abs col" style="left:925px"><h4>Customer Care</h4><p>Order Info<br>Shipping / Tracking<br>Returns Info<br>Request Exchange<br>Guarantee</p></div>
  <div class="abs rule"></div>
  <div class="abs social"><span></span><span></span><span></span><span></span></div>
  <div class="abs copy">Copyright © 2019 All Rights reserved.Privacy Policy &nbsp;&nbsp; Terms &amp; Conditions</div>
</footer>

</body>
</html>
```